Copperleaf Venture Trust

Take current power point presentation and make it uniform in color and font, and create designs that pop throughout the presentation. Right now, it is dull and mundane.

```html
<!DOCTYPE html>
<html lang="en">
<head>
<meta charset="utf-8">
<title>Copperleaf Venture Trust – Presentation Overview</title>
<link href="https://fonts.googleapis.com/css2?family=Roboto:wght@300;400;500;700&display=swap" rel="stylesheet">
<style>
:root{
  --blue:#0d5db8;
  --blue-dark:#0a4f9e;
  --ink:#111;
  --muted:#333;
  --white:#fff;
  --stage:#000;
  --deep:#1c1f22;
  --rule:#222;
}
*{box-sizing:border-box;margin:0;padding:0}
html,body{width:1036px;height:1200px;overflow:hidden;background:var(--stage)}
body{position:relative;font-family:'Roboto',Arial,sans-serif;color:var(--ink)}
.slide{position:absolute;width:460px;height:259px;background:var(--white);overflow:hidden}
.col-l{left:48px}.col-r{left:528px}
.row-1{top:55px}.row-2{top:329px}.row-3{top:609px;height:264px}.row-4{top:893px}
.bar{position:absolute;left:0;top:0;width:100%;height:23px;background:var(--blue);color:var(--white);font-weight:300;font-size:12px;line-height:23px;padding-left:7px}
.wordmark{font-weight:700;color:var(--blue);letter-spacing:.2px}

/* cover */
.cover{background:var(--deep)}
.cover .wordmark{position:absolute;left:32px;top:100px;font-size:23px;line-height:27px;width:180px}
.cover .photo{position:absolute;left:235px;top:0;width:225px;height:259px;background:radial-gradient(circle at 45% 40%,#8a5a30 0%,#3a2c24 30%,#1c1f22 70%)}

/* disclosure */
.disclosure .body{position:absolute;left:16px;top:46px;right:18px;font-size:6.4px;line-height:9.5px;color:var(--muted)}
.disclosure p{margin-bottom:9.5px}

/* agenda */
.agenda .item{position:absolute;left:0;right:0;border-bottom:.7px solid var(--rule);font-size:8.4px}
.agenda .item span{position:absolute;left:27px}
.agenda .item b{position:absolute;right:14px;font-weight:400;color:var(--blue)}
.agenda .sub{position:absolute;left:29px;font-size:6.6px;color:var(--muted)}
.agenda .sub::before{content:"";display:inline-block;border-left:3.5px solid var(--blue);border-top:2.3px solid transparent;border-bottom:2.3px solid transparent;margin-right:5px;vertical-align:0}

/* strategy */
.strategy .photo{position:absolute;left:0;top:23px;width:209px;height:236px;background:linear-gradient(160deg,#1a3550 0%,#2d6a8f 45%,#0f2436 100%)}
.strategy h2{position:absolute;left:221px;top:37px;font-size:11.5px;font-weight:700}
.strategy .lead{position:absolute;left:221px;top:59px;width:200px;font-size:6.9px;line-height:9.7px}
.objectives{position:absolute;left:221px;top:114px;right:0;bottom:0;background:var(--blue);color:var(--white)}
.objectives h3{position:absolute;left:12px;top:10px;font-size:11.5px;font-weight:700}
.objectives .tag{position:absolute;left:12px;top:26px;font-size:6.6px}
.obj{position:absolute;top:50px;width:72px;height:80px;padding-left:0}
.obj svg{display:block;width:20px;height:20px;margin-bottom:12px}
.obj h4{font-size:6.9px;font-weight:700;margin-bottom:4px}
.obj p{font-size:5.6px;line-height:7.6px}
.obj.sep{border-left:.8px solid rgba(255,255,255,.8);padding-left:12px}

/* organization divider */
.org .top{position:absolute;left:0;top:0;width:100%;height:101px;background:var(--white)}
.org .top .wordmark{position:absolute;left:0;right:0;top:38px;text-align:center;font-size:17px}
.org .band{position:absolute;left:0;top:101px;width:100%;bottom:0;background:var(--blue);color:var(--white);text-align:center}
.org h1{margin-top:44px;font-size:25px;font-weight:700;letter-spacing:1.4px}
.org .subtitle{margin-top:10px;font-size:10.5px;font-weight:500;letter-spacing:.6px}

/* senior management */
.person{position:absolute;left:17px;right:16px;height:60px}
.person .portrait{position:absolute;left:0;top:0;width:43px;height:52px;background:linear-gradient(180deg,#cfcfcf,#5d5d5d)}
.person h3{position:absolute;left:52px;top:3px;font-size:8px;font-weight:700;color:var(--blue)}
.person p{position:absolute;left:52px;top:15px;right:0;font-size:4.7px;line-height:7.6px;color:var(--muted)}

/* different */
.different .text{position:absolute;left:0;top:23px;width:207px;bottom:0;padding:18px 14px 0 21px}
.different h2{font-size:10.4px;font-weight:700;color:var(--blue);margin-bottom:10px}
.different p{font-size:6.4px;line-height:9.2px;margin-bottom:8.5px}
.different p b{color:var(--blue);font-weight:700}
.different .photo{position:absolute;left:207px;top:23px;right:0;bottom:0;background:linear-gradient(150deg,#3d3a33 0%,#1f2530 45%,#9fb4c9 75%,#2a2e35 100%)}

/* closing */
.closing{background:var(--blue);color:var(--white);text-align:center}
.closing .wordmark{position:absolute;left:0;right:0;top:56px;color:var(--white);font-size:20px}
.closing .rule{position:absolute;left:150px;width:164px;height:1.2px;background:var(--white)}
.closing .thanks{position:absolute;left:0;right:0;top:144px;font-size:34px;font-weight:300}
</style>
</head>
<body>

<section class="slide cover col-l row-1">
  <div class="wordmark">Copperleaf Venture Trust</div>
  <div class="photo" role="img" aria-label="Hand holding stacks of coins with a rising financial chart arrow"></div>
</section>

<section class="slide disclosure col-r row-1">
  <div class="bar">Disclosure</div>
  <div class="body">
    <p>This Presentation is a summary and does not constitute an offer to sell, or a solicitation of any offer to buy or sell, any securities. Any such offer will be made solely to qualified investors by means of an offering memorandum and related subscription materials, which will contain material information not contained herein. This Presentation is not intended to replace any such offering memorandum.</p>
    <p>No assurance can be given that the objectives discussed herein will be achieved and results may vary substantially on a quarterly, annual or other periodic basis. Past performance is not necessarily indicative of future results.</p>
    <p>Prospective reviewers should not construe this Presentation, any offering memorandum or any other communication received from CVT or its affiliates as legal, accounting, tax, investment or other advice, and each reviewer should consult with its own counsel and advisors as to all legal, tax, regulatory, financial and related matters.</p>
    <p>In addition, certain information contained herein has been provided by third parties and has not been independently verified by CVT. CVT makes no representation or warranty, express or implied, as to the accuracy or the completeness of such information, and accepts no liability for any direct or consequential losses arising from the use of such information.</p>
    <p>This Presentation is confidential and proprietary to CVT. Accordingly, this Presentation is to be treated as strictly confidential and not disclosed, directly or indirectly, to any party other than the person to whom it has been delivered and such person’s professional advisors. Any distribution of this Presentation, in whole or in part, or the divulgence of any of its contents, is unauthorized. No person has been authorized to give any information or make any representations other than as set forth herein.</p>
  </div>
</section>

<section class="slide agenda col-l row-2">
  <div class="bar">Agenda</div>
  <div class="item" style="top:34px;height:15px"><span>Objectives</span><b>4</b></div>
  <div class="item" style="top:53px;height:15px"><span>Strategy</span><b>5</b></div>
  <div class="item" style="top:72px;height:48px"><span>The CVT organization</span><b>6</b></div>
  <div class="sub" style="top:86px">Senior Management</div>
  <div class="sub" style="top:97px">CVT’s competitive advantage</div>
  <div class="sub" style="top:108px">How we are different</div>
  <div class="item" style="top:125px;height:15px"><span>Performance</span><b>12</b></div>
  <div class="item" style="top:144px;height:15px"><span>Structure &amp; Terms</span><b>19</b></div>
  <div class="item" style="top:163px;height:0;border:0"><span>Why Direct Investments?</span><b>20</b></div>
  <div class="sub" style="top:178px">Why CVT’ Direct Invest Strategy?</div>
  <div class="sub" style="top:189px">Industry Overview</div>
  <div class="sub" style="top:200px">Differentiation Between PIPEs and Direct Investments</div>
  <div class="sub" style="top:211px">Capital/Deal Structure</div>
  <div class="sub" style="top:222px">Process</div>
  <div class="sub" style="top:233px">Protection/Risk</div>
</section>

<section class="slide strategy col-r row-2">
  <div class="bar">Investment Strategy</div>
  <div class="photo" role="img" aria-label="Businessman with open hands beneath a glowing holographic bar chart"></div>
  <h2>CVT Funding Specialization</h2>
  <p class="lead">CVT focuses on financing Development Stage, Emerging Growth, and Distressed public companies. This is achieved through a structured approach, wherein investments are tranched over a one- to four-year timeframe.</p>
  <div class="objectives">
    <h3>Objectives</h3>
    <div class="tag">Our strategy serves three key purposes</div>
    <div class="obj" style="left:12px">
      <svg viewBox="0 0 20 20" fill="#fff"><rect x="1" y="6" width="7" height="9"/><rect x="12" y="6" width="7" height="9"/><rect x="9.2" y="1" width="1.6" height="18"/></svg>
      <h4>Minimize Dilution</h4>
      <p>Limits the dilution of the issuer’s common stock</p>
    </div>
    <div class="obj sep" style="left:80px">
      <svg viewBox="0 0 20 20" fill="#fff"><path d="M1 9a9 7 0 0 1 18 0z"/><circle cx="6" cy="14" r="3" fill="none" stroke="#fff" stroke-width="1.6"/><circle cx="14" cy="14" r="3" fill="none" stroke="#fff" stroke-width="1.6"/><rect x="9.3" y="9" width="1.4" height="6"/></svg>
      <h4>Mitigate Risk</h4>
      <p>Reduces exposure by allowing cessation of further investment in the event of a material adverse change.</p>
    </div>
    <div class="obj sep" style="left:160px">
      <svg viewBox="0 0 20 20"><circle cx="10" cy="10" r="7.5" fill="none" stroke="#fff" stroke-width="3" stroke-dasharray="3 1.6"/><circle cx="10" cy="10" r="5" fill="none" stroke="#fff" stroke-width="1.2"/><text x="10" y="12.6" font-size="7" font-family="Roboto,sans-serif" font-weight="700" fill="#fff" text-anchor="middle">$</text></svg>
      <h4>Protect Capital</h4>
      <p>Safeguards against losses stemming from fraud or corporate malfeasance</p>
    </div>
  </div>
</section>

<section class="slide org col-l row-3">
  <div class="top"><div class="wordmark">Copperleaf Venture Trust</div></div>
  <div class="band">
    <h1>THE ORGANIZATION</h1>
    <div class="subtitle">CVT’S COMPETITIVE ADVANTAGE: WHAT SETS US APART</div>
  </div>
</section>

<section class="slide management col-r row-3">
  <div class="bar">Senior Management</div>
  <div class="person" style="top:32px">
    <div class="portrait" role="img" aria-label="Portrait photo of Daniel Reyes"></div>
    <h3>Daniel Reyes</h3>
    <p>Daniel Reyes is a Founder and Member of CVT Investments LLC, bringing over 17 years of experience in PIPE (Private Investment in Public Equity) transactions. Prior to launching his own funds, Mr. Reyes co-founded multiple investment funds and managed portfolios for a boutique family of funds. Before joining the family of funds in 2009, he worked as an analyst for an $800 million hedge fund based in Eastport, New York, where he oversaw fifty-five portfolio companies with a focus on private equity financing. Mr. Reyes holds a Bachelor of Arts in Finance from Northfield State University.</p>
  </div>
  <div class="person" style="top:97px">
    <div class="portrait" role="img" aria-label="Portrait photo of Omar Castell"></div>
    <h3>Omar Castell</h3>
    <p>Omar Castell is a Founder and Member of CVT Investments LLC with extensive experience investing in publicly traded companies since 2011. In addition to co-founding multiple investment funds, Mr. Castell’s professional background spans roles at a New York State Agency, a class action administration firm, and an I.T. company prior to his transition into finance. Mr. Castell earned his Juris Doctor (J.D.) from Eastbrook University and holds a Bachelor’s degree in Philosophy, Politics, and Law from Northfield State University.</p>
  </div>
  <div class="person" style="top:166px">
    <div class="portrait" role="img" aria-label="Portrait photo of Peter Lindqvist"></div>
    <h3>Peter Lindqvist</h3>
    <p>Peter Lindqvist is a business executive with extensive C-level and Board of Director leadership experience across multiple privately and publicly held companies. He is currently a Founder and Member of CVT Investments LLC. Previously, Mr. Lindqvist was the Founder, Chairman, and Chief Executive Officer of Nova Cell Storage, Inc. (NCSI), a company specializing in harvesting and storing stem cells in the U.S. and internationally, from 2003 to 2012. He also concurrently served as CEO and Chairman of Helix Partners Inc., later absorbed by NCSI in 2005, and as Founder and President of Eastern Cell Bank, Inc., a stem cell storage facility in northeastern Asia. Before joining CVT, Mr. Lindqvist worked as a licensed investment banker with Crestline Advisory, LLC, providing microcap advisory and capital introduction services to publicly traded companies. In this role, he cultivated relationships with hedge funds, venture capital funds, family offices, and other institutional investors. Mr. Lindqvist currently serves on the Special Council of the National Policy Council and has previously held leadership positions as Chairman of the Regional Development Authority Biotech Committees and as a board member of the Lakeside Natural History Museum. He holds a Bachelor of Arts in Biology from Ridgemont College.</p>
  </div>
</section>

<section class="slide different col-l row-4">
  <div class="bar">How We Are Different</div>
  <div class="text">
    <h2>Our Distinctive Approach</h2>
    <p>Unlike many funds that adhere to a rigid transaction structure, CVT collaborates directly with each company to customize investment structures and strategies that align with mutual objectives.</p>
    <p><b>Focused Portfolio:</b> We prioritize a smaller portfolio to maximize returns for each Investment.</p>
    <p><b>Problem-Solving Strategy:</b> Our approach is centered on addressing challenges and/or supporting milestones to unlock each company’s full potential</p>
    <p><b>Efficient Processes:</b> CVT employs internal due diligence and document review procedures to ensure cost-effective and timely execution of opportunities.</p>
    <p><b>Robust Network:</b> We leverage our established network of professionals and investment partners to explore new opportunities.</p>
  </div>
  <div class="photo" role="img" aria-label="Hand touching a tablet showing a financial analytics dashboard"></div>
</section>

<section class="slide closing col-r row-4">
  <div class="wordmark">Copperleaf Venture Trust</div>
  <div class="rule" style="top:136px"></div>
  <div class="thanks">Thank You</div>
  <div class="rule" style="top:198px"></div>
</section>

</body>
</html>
```